Bifold brochure design for leadership academy

Please see below. This is a bifold brochure for a leadership academy. (www.brv.institute). Look and feel must be colours, shapes, abstract designs, graphics, pictures. Make this professional, yet casual and bold.

Feel free to design just the front and back cover, then I'll give feedback on whether or not you're in the right direction.

COVER
- Title: “The Boldest Bridge Year Journey”
- “Northward Mentor Institute” logo somewhere
- Subtitles (with images, icons, and/or shapes): “Self-discovery” “Skills development” “Real-world Impact”

PAGE 2 (Inside Fold)
- Title: "The Program"
- Section 2a: Section title: "How it works”
- Image: See website, image under "four phases of the program". Please adapt and make it look better
- Text: NMI is a structured, 8-month ‘gap year’ program for 18-25 year olds who want more than just a year off – they want a year ahead. Our aim is to develop high-potential young leaders with strong values, clear purpose, high-impact skills, and a track record of real-world accomplishments that are second-to-none. We do this through four-phases.
- Section 2b: Section title: “Dates & Timing”
- Image: See image on website under 'dates and timing'. Make sure both dates show up on the brochure (September and January program).
- Text: There are two programs per year: one that starts in September, the other in January. The first four months of the program are based in Toronto at the NMI headquarters. The curriculum we work through is highly engaging and personalized, focusing directly on students’ goals. After that, students are out in the world, achieving the remaining components of the program (e.g. internship, volunteer abroad).

PAGE 3 (Outside Fold)
- Page Title: "The Students"
- Section 3a: Section title: “Who’s it for”
- Subtitle1: “High school graduates”
 Image/icon of a high school grad
 Text1: 90% of high school grads aren't sure why they’re going to university or what they want to study.
 Text2: NMI helps students discover what they truly want to do in life, and make enormous progress towards these goals.

- Subtitle2: “Post-secondary students”
 Image/icon of a university / college student
 Text1: 28% of students switch or drop out of their program because it wasn’t for them or they didn’t like it.
 Text2: Don't keep moving around or risk switching careers down the road – find out what sparks your passion with NMI.

- Subtitle3: “Post-secondary graduates”
 Image/icon of a university/ college grad
 Text1: 50% of graduates are unemployed or underemployed, 60% are in debt.
 Text2: NMI will help you get your dream job – our students won’t settle for anything less.

- Section 3b: Section title: “How to apply”
 Text1: We select high-potential young leaders with a desire to improve themselves and impact the world.
 Text2: We won’t ask you for your grades – we care more about your values and potential.
 Text3: Visit www.brv.institute to apply now

BACK COVER
- Page Title: “Get in Touch”
- Website: www.brv.institute
- Facebook page: facebook.com/brv.institute
- Twitter handle: @brv_institute
- Email: tomas@brv.institute

Project Deadline Extended Reason: Made a mistake initially only giving designers 2 days to submit. This allows for more high quality designs. Thank you. Added Wednesday, March 18, 2015

Target Market(s)

18-25 year olds, parents, teachers

Industry/Entity Type

Leadership

Requirements
Must have
• Beautiful design - sleek and bold, yet colourful and casual. Keep the colours similar to our website (www.brv.institute). See examples of other brochures.
• http://img.pelvoro.net/jpg/00/11/22/33/240_F_11223344_xQr8LmPzTw3KdNvBsYcHuJeFa2gkTqWn.jpg
• http://vantoliq.com/wp-content/uploads/2014/11/Real-Estate-Bi-fold-Brochure.jpg
• http://www.murablo.com/media/k2/galleries/5/001-bi-fold-brochure-psd-mock-up-template.jpg
• http://img.pelvoro.net/jpg/00/44/55/66/240_F_44556677_Zk3wPqLm8RtYvBnXcDs2HjKuE5fa9Gq0.jpg

```html
<!DOCTYPE html>
<html lang="en">
<head>
<meta charset="utf-8">
<title>Northward Mentor Institute – Bifold Brochure Inside Spread</title>
<link rel="stylesheet" href="https://fonts.googleapis.com/css2?family=Arimo:wght@400;700&family=Raleway:wght@300;400;500&display=swap">
<style>
  :root {
    --navy: #2f3a8c;
    --red: #c8191e;
    --red-dark: #a3141a;
    --red-soft: #e04a4a;
    --red-pale: #e8a0a0;
    --green: #6c9a3a;
    --ink: #3a3a3a;
    --grey: #5b5b5b;
    --paper: #ffffff;
    --backdrop: #eceef1;
  }
  * { box-sizing: border-box; margin: 0; padding: 0; }
  html, body { width: 1200px; height: 780px; overflow: hidden; }
  body {
    background: var(--backdrop);
    font-family: "Raleway", Arial, sans-serif;
    color: var(--ink);
    position: relative;
  }
  .spread {
    position: absolute; left: 55px; top: 28px;
    width: 1055px; height: 724px;
    background: var(--paper);
    box-shadow: 0 4px 14px rgba(0,0,0,.25);
    overflow: hidden;
  }
  .spread__shapes { position: absolute; inset: 0; }
  .abs { position: absolute; }

  .page-tab {
    position: absolute; font-family: "Arimo", Arial, sans-serif;
    font-weight: 700; font-size: 21px; line-height: 28px;
  }
  .page-tab--program { left: 3px; top: 2px; width: 163px; padding-left: 3px; background: var(--paper); color: #111; border-bottom: 3px solid var(--red); }
  .page-tab--students { left: 859px; top: 0; width: 176px; text-align: center; background: var(--navy); color: #fff; box-shadow: 3px 3px 0 var(--red); }

  .how-title { left: 5px; top: 37px; color: #fff; font-family: "Arimo", Arial, sans-serif; font-weight: 700; font-size: 16px; line-height: 18px; }
  .how-sub { left: 5px; top: 54px; color: #fff; font-family: "Arimo", Arial, sans-serif; font-size: 10px; line-height: 12px; }

  .phases {
    left: 8px; top: 73px; width: 479px; height: 258px;
    background: var(--paper); display: grid; grid-template-columns: repeat(4, 1fr);
  }
  .phase { border-right: 1px solid #e3e3e3; display: flex; flex-direction: column; }
  .phase:last-child { border-right: 0; }
  .phase__head {
    background: var(--red); color: #fff; font-family: "Arimo", Arial, sans-serif;
    font-weight: 700; font-size: 13px; height: 22px; line-height: 22px; padding-left: 6px;
  }
  .phase:last-child .phase__head { background: var(--red-soft); }
  .phase__art { margin: 6px auto 0; }
  .phase__text { font-size: 9.2px; line-height: 13px; padding: 4px 3px 0 3px; color: var(--ink); }
  .feats { list-style: none; font-size: 8.8px; line-height: 19px; padding: 0 3px; }
  .feats li::before { content: ""; display: inline-block; width: 5px; height: 5px; border-radius: 50%; background: #8aa3b8; margin-right: 4px; vertical-align: middle; }

  .intro {
    left: 121px; top: 346px; width: 368px;
    font-size: 10.8px; line-height: 12.6px; color: #333;
  }

  .dates {
    left: 8px; top: 440px; width: 308px; height: 254px;
    background: var(--paper); border: 1px solid #7b80b5; border-radius: 10px;
  }
  .dates__title { position: absolute; left: 12px; top: 4px; font-family: "Arimo", Arial, sans-serif; font-weight: 400; font-size: 22px; color: #222; }
  .dates svg { position: absolute; left: 0; top: 0; }

  .calendar { font-family: "Arimo", Arial, sans-serif; }
  .dates-copy {
    left: 330px; top: 492px; width: 163px;
    color: #fff; font-size: 10.6px; line-height: 12.4px; letter-spacing: .6px; text-align: justify;
  }
  .dates-copy p + p { margin-top: 12px; }

  .who-title { left: 546px; top: 55px; font-family: "Arimo", Arial, sans-serif; font-weight: 700; font-size: 21px; color: var(--navy); }
  .who-rule { left: 544px; top: 80px; width: 511px; height: 1px; background: #e2e2e2; }
  .group { position: absolute; left: 545px; width: 320px; }
  .group__title { font-family: "Arimo", Arial, sans-serif; font-weight: 700; font-size: 14px; color: #555; margin-bottom: 3px; }
  .group__title--caps { text-transform: uppercase; }
  .group p { font-size: 10.8px; line-height: 12.6px; color: var(--grey); }
  .group p + p { margin-top: 12px; }
  .photo { position: absolute; border: 3px solid var(--navy); }

  .apply-title { left: 561px; top: 526px; color: #fff; font-family: "Arimo", Arial, sans-serif; font-weight: 400; font-size: 29px; }
  .apply-copy { left: 561px; top: 570px; color: #fff; font-family: "Arimo", Arial, sans-serif; font-size: 9.6px; line-height: 16.2px; }
  .badges { left: 561px; top: 672px; display: flex; gap: 6px; align-items: center; }
  .badge { background: var(--paper); height: 25px; border: 1px solid #d9d9d9; }
</style>
</head>
<body>
<main class="spread">
  <svg class="spread__shapes" width="1055" height="724" viewBox="0 0 1055 724" aria-hidden="true">
    <!-- left page -->
    <polygon points="0,0 528,0 528,78 0,102" fill="var(--navy)"/>
    <polygon points="360,0 528,0 528,112 470,108" fill="var(--red)"/>
    <polygon points="0,96 528,70 528,330 0,330" fill="var(--red)"/>
    <polygon points="487,90 528,88 528,330 487,330" fill="var(--red-pale)"/>
    <polygon points="0,330 528,330 528,440 0,440" fill="var(--red)"/>
    <polygon points="112,336 528,326 528,402 112,412" fill="var(--paper)"/>
    <polygon points="0,440 528,400 528,724 0,724" fill="var(--red)"/>
    <polygon points="300,420 528,410 528,560 330,470" fill="var(--red-dark)"/>
    <polygon points="0,610 150,724 0,724" fill="var(--navy)"/>
    <polygon points="260,724 528,600 528,724" fill="var(--navy)"/>
    <polygon points="420,500 528,520 528,620" fill="var(--red-soft)" opacity=".6"/>
    <!-- right page -->
    <polygon points="528,0 560,0 528,40" fill="var(--red)"/>
    <polygon points="528,470 1055,480 1055,724 528,724" fill="var(--red)"/>
    <polygon points="528,470 760,560 528,600" fill="var(--red-dark)"/>
    <polygon points="528,610 730,724 528,724" fill="var(--navy)"/>
    <polygon points="1000,490 1055,480 1055,724 980,724" fill="var(--navy)"/>
    <polygon points="820,600 1000,520 980,724 760,724" fill="var(--red-dark)" opacity=".7"/>
    <line x1="528" y1="0" x2="528" y2="724" stroke="rgba(0,0,0,.08)"/>
  </svg>

  <div class="page-tab page-tab--program">The Program</div>
  <div class="abs how-title">How it works</div>
  <div class="abs how-sub">FOUR PHASES OF THE PROGRAM</div>

  <section class="abs phases">
    <div class="phase">
      <div class="phase__head">1. Discover</div>
      <div class="phase__art" role="img" aria-label="Compass illustration for self-discovery" style="width:84px;height:84px;border-radius:50%;background:radial-gradient(circle,#6f9ec4 0 45%,#c9cdd2 46% 100%);"></div>
      <p class="phase__text">Discover your strengths, development areas, personality style, passions and other attributes through a highly personalized transformation program.</p>
    </div>
    <div class="phase">
      <div class="phase__head">2. Design</div>
      <div class="phase__art" role="img" aria-label="Target with darts illustration for goal setting" style="width:100px;height:76px;background:linear-gradient(135deg,#f3f3f3,#e04646 60%,#3e6bb0);"></div>
      <p class="phase__text">Design your year in the program and learn how to manage goals through our advanced goal-setting training.</p>
    </div>
    <div class="phase">
      <div class="phase__head">3. Build</div>
      <div class="phase__art" role="img" aria-label="Photo of a teacher leading a classroom session" style="width:106px;height:70px;background:linear-gradient(135deg,#b9b3a6,#5c5a55);"></div>
      <p class="phase__text">Build a set of skills that will directly help you achieve your goals, including issue-based problem solving, creativity, and tructured communications.</p>
    </div>
    <div class="phase">
      <div class="phase__head">4. Achieve</div>
      <div class="phase__art" role="img" aria-label="Icons for the six achievements" style="width:106px;height:62px;background:linear-gradient(135deg,#e8e8e8,#c9d9e6);"></div>
      <p class="phase__text">Achieve six things before you can graduate:</p>
      <ul class="feats">
        <li>1. Solve a social problem</li>
        <li>2. Conquer a physical feat</li>
        <li>3. Organize an event</li>
        <li>4. Volunteer abroad</li>
        <li>5. Start something</li>
        <li>6. Do an internship</li>
      </ul>
    </div>
  </section>

  <p class="abs intro">NMI is a structured, 8-month ‘gap year’ program for 18-25 year olds who want more than just a year off – they want a year ahead. Our aim is to develop high-potential young leaders with strong values, clear purpose, high-impact skills, and a track record of real-world accomplishments that are second-to-none. We do this through four-phases.</p>

  <section class="abs dates">
    <h2 class="dates__title">Dates &amp; Timing</h2>
    <svg width="308" height="254" viewBox="0 0 308 254" font-family="Arimo, Arial, sans-serif">
      <text x="4" y="37" font-size="4.5" fill="#444">PREP WORK</text>
      <text x="8" y="42" font-size="4.5" fill="#444">ONLINE</text>
      <text x="40" y="39" font-size="4.5" fill="#444">FULL TIME IN CLASSROOM</text>
      <line x1="34" y1="42" x2="128" y2="42" stroke="#555" stroke-width=".6"/>
      <text x="165" y="39" font-size="4.5" fill="#444">MONTHLY CHECKPOINTS</text>
      <line x1="138" y1="42" x2="300" y2="42" stroke="#555" stroke-width=".6"/>
      <g font-size="8" fill="#333">
        <text x="6" y="54">Aug</text><text x="33" y="54">Sep</text><text x="59" y="54">Oct</text>
        <text x="85" y="54">Nov</text><text x="110" y="54">Dec</text><text x="136" y="54">Jan</text>
        <text x="161" y="54">Feb</text><text x="187" y="54">Mar</text><text x="213" y="54">Apr</text>
        <text x="238" y="54">May</text><text x="264" y="54">Jun</text><text x="289" y="54">Jul</text>
      </g>
      <rect x="6" y="92" width="22" height="22" fill="#fff" stroke="#777" stroke-width=".8"/>
      <text x="9" y="106" font-size="7" font-weight="700" fill="#333">NMI</text>
      <rect x="28" y="94" width="44" height="8" fill="var(--green)"/>
      <text x="30" y="100" font-size="4.5" fill="#fff">DISCOVER</text>
      <rect x="28" y="103" width="44" height="8" fill="#8db25e"/>
      <text x="30" y="109" font-size="4" fill="#fff">Find your purpose</text>
      <circle cx="40" cy="124" r="8" fill="#5b7fb5"/>
      <rect x="48" y="119" width="22" height="10" fill="#9aa3ad"/>
      <text x="50" y="126" font-size="4.5" fill="#fff">Design goals</text>
      <circle cx="40" cy="149" r="8" fill="var(--navy)"/>
      <text x="54" y="144" font-size="4.5" fill="#333">BUILD</text>
      <rect x="52" y="146" width="56" height="9" fill="var(--navy)"/>
      <text x="54" y="152" font-size="4" fill="#fff">Build relevant skills for life</text>
      <text x="138" y="143" font-size="4.5" fill="#333">MONTHLY CHECKPOINTS</text>
      <g fill="var(--navy)">
        <rect x="139" y="146" width="3" height="9"/><rect x="165" y="146" width="3" height="9"/>
        <rect x="190" y="146" width="3" height="9"/><rect x="216" y="146" width="3" height="9"/>
      </g>
      <circle cx="40" cy="175" r="9" fill="var(--red)"/>
      <text x="52" y="169" font-size="4.5" fill="#333">ACHIEVE</text>
      <rect x="50" y="172" width="76" height="9" fill="var(--red)"/>
      <text x="53" y="178" font-size="5" fill="#fff">Solve a social problem</text>
      <circle cx="40" cy="200" r="8" fill="#e0a540"/>
      <rect x="50" y="196" width="76" height="9" fill="var(--red)"/>
      <text x="53" y="202" font-size="5" fill="#fff">Conquer a physical feat</text>
      <circle cx="46" cy="226" r="8" fill="#7fb3d9"/>
      <rect x="54" y="222" width="72" height="9" fill="var(--red)"/>
      <text x="57" y="228" font-size="5" fill="#fff">Organize an Event</text>
      <circle cx="196" cy="175" r="8" fill="var(--red)"/>
      <rect x="204" y="171" width="76" height="9" fill="var(--red)"/>
      <text x="207" y="177" font-size="5" fill="#fff">On an internship</text>
      <circle cx="142" cy="200" r="8" fill="var(--red)"/>
      <rect x="150" y="196" width="76" height="9" fill="var(--red)"/>
      <text x="153" y="202" font-size="5" fill="#fff">Volunteer abroad</text>
      <circle cx="142" cy="226" r="8" fill="var(--red)"/>
      <rect x="150" y="222" width="100" height="9" fill="var(--red)"/>
      <text x="153" y="228" font-size="5" fill="#fff">Start something</text>
    </svg>
  </section>

  <svg class="abs calendar" style="left:385px;top:442px" width="90" height="42" viewBox="0 0 90 42">
    <rect x="0" y="0" width="40" height="40" rx="3" fill="#fff" stroke="#ccc"/>
    <rect x="0" y="0" width="40" height="12" rx="3" fill="var(--red)"/>
    <text x="20" y="29" font-size="6.5" text-anchor="middle" fill="#222">September</text>
    <rect x="46" y="0" width="40" height="40" rx="3" fill="#fff" stroke="#ccc"/>
    <rect x="46" y="0" width="40" height="12" rx="3" fill="var(--red)"/>
    <text x="66" y="29" font-size="6.5" text-anchor="middle" fill="#222">January</text>
  </svg>

  <div class="abs dates-copy">
    <p>There are two programs per year: one that starts in September, the other in January.</p>
    <p>The first four months of the program are based in Toronto at the NMI headquarters.</p>
    <p>The curriculum we work through is highly engaging and personalized, focusing directly on students’ goals. After that, students are out in the world, achieving the remaining components of the program (e.g. internship, volunteer abroad).</p>
  </div>

  <div class="page-tab page-tab--students">The Students</div>
  <h2 class="abs who-title">Who’s it for</h2>
  <div class="abs who-rule"></div>

  <section class="group" style="top:95px">
    <h3 class="group__title group__title--caps">High school graduates</h3>
    <p>90% of high school grads aren’t sure why they’re going to university or what they want to study.</p>
    <p>NMI helps students discover what they truly want to do in life, and make enormous progress towards these goals.</p>
  </section>
  <div class="photo" role="img" aria-label="Photo of a high school graduate studying" style="left:923px;top:90px;width:125px;height:84px;background:linear-gradient(135deg,#8a93a8,#d8dbe3);"></div>

  <section class="group" style="top:202px">
    <h3 class="group__title">Post-secondary students</h3>
    <p>28% of students switch or drop out of their program because it wasn’t for them or they didn’t like it.</p>
    <p>Don’t keep moving around or risk switching careers down the road – find out what sparks your passion with NMI.</p>
  </section>
  <div class="photo" role="img" aria-label="Photo of university students in caps and gowns" style="left:923px;top:200px;width:125px;height:83px;background:linear-gradient(135deg,#3a3a44,#8db0d8);"></div>

  <section class="group" style="top:360px">
    <h3 class="group__title">Post-secondary graduates</h3>
    <p>50% of graduates are unemployed or underemployed, 60% are in debt.</p>
    <p>NMI will help you get your dream job – our students won’t settle for anything less.</p>
  </section>
  <div class="photo" role="img" aria-label="Photo of a group of college graduates celebrating" style="left:915px;top:355px;width:133px;height:78px;background:linear-gradient(135deg,#4f7a3a,#2b2b30);"></div>

  <h2 class="abs apply-title">How to apply</h2>
  <div class="abs apply-copy">
    <p>We select high-potential young leaders with a desire to improve themselves and impact the world.</p>
    <p>We won’t ask you for your grades – we care more about your values and potential.</p>
    <p>Visit www.brv.institute to apply now</p>
  </div>

  <div class="abs badges" aria-label="Media features">
    <div class="badge" style="width:76px"></div>
    <div class="badge" style="width:32px"></div>
    <div class="badge" style="width:88px"></div>
    <div class="badge" style="width:48px"></div>
    <div class="badge" style="width:46px"></div>
  </div>
</main>
</body>
</html>
```